SkyvornQ Business Cards and Stationary Design

Need a design for our business cards and stationary. I want to carry on the theme of the logo. I want the business cards to have a design on the back. I would like the business cards and the stationary to carry the same theme, design scheme, and branding

Target Market(s)

Airlines and Maintenance Facilities

Industry/Entity Type

Aviation

Contact Information for Business Card

Name
Position Title
Address: 4827 Trellis Hollow Road, Fort Pierce, Florida, 34951
Office Number
Mobile Number
Email
Website

Font styles to use
Serif
Sans Serif

Colors

Designer to choose colors to be used in the design.

```html
<!DOCTYPE html>
<html lang="en">
<head>
<meta charset="utf-8">
<title>SkyvornQ Business Card</title>
<link rel="stylesheet" href="https://fonts.googleapis.com/css2?family=Open+Sans:wght@400;700&family=Oswald:wght@300;500&display=swap">
<style>
  :root {
    --navy: #14284b;
    --navy-deep: #132a4e;
    --sky: #2a8fd0;
    --ink-grey: #555a60;
    --divider: #c9ccd0;
    --backdrop-light: #e8e9ea;
    --backdrop-dark: #d0d1d3;
    --white: #ffffff;
  }
  html, body {
    margin: 0;
    padding: 0;
    width: 1200px;
    height: 1103px;
    overflow: hidden;
  }
  body {
    background: linear-gradient(135deg, var(--backdrop-light), var(--backdrop-dark));
    position: relative;
  }
  .card {
    position: absolute;
    width: 762px;
    height: 435px;
    border-radius: 27px;
    overflow: hidden;
  }
  .card svg { display: block; width: 762px; height: 435px; }
  .card-front { left: 386px; top: 85px; background: var(--white); box-shadow: 0 0 0 1px #3a3a3a; }
  .card-back { left: 82px; top: 562px; background: var(--navy-deep); }
  .brand-name { font-family: "Open Sans", sans-serif; font-weight: 700; }
  .holder-name { font-family: "Oswald", sans-serif; font-weight: 500; font-size: 27px; fill: var(--navy); letter-spacing: 0.5px; }
  .holder-title { font-family: "Oswald", sans-serif; font-weight: 300; font-size: 24px; fill: var(--ink-grey); letter-spacing: 0.5px; }
  .contact-line { font-family: "Open Sans", sans-serif; font-size: 17.5px; fill: var(--navy); }
  .address-line { font-family: "Open Sans", sans-serif; font-size: 17px; fill: var(--white); }
  .back-url { font-family: "Open Sans", sans-serif; font-size: 23px; fill: var(--white); letter-spacing: 5px; }
</style>
</head>
<body>

<div class="card card-front">
  <svg viewBox="0 0 762 435" xmlns="http://www.w3.org/2000/svg">
    <defs>
      <linearGradient id="swoosh-gradient" x1="0" y1="0" x2="1" y2="0">
        <stop offset="0" stop-color="var(--navy)"/>
        <stop offset="1" stop-color="var(--sky)"/>
      </linearGradient>
      <linearGradient id="ring-gradient" x1="0" y1="0" x2="1" y2="1">
        <stop offset="0" stop-color="var(--sky)"/>
        <stop offset="1" stop-color="var(--navy)"/>
      </linearGradient>
    </defs>

    <g class="brand-block">
      <circle cx="235" cy="150" r="48" fill="none" stroke="url(#ring-gradient)" stroke-width="6"/>
      <text class="brand-name" x="235" y="248" text-anchor="middle" font-size="38" fill="var(--navy)" letter-spacing="4">SkyvornQ</text>
    </g>

    <line x1="434" y1="85" x2="434" y2="270" stroke="var(--divider)" stroke-width="2"/>

    <g class="holder">
      <text class="holder-name" x="460" y="106">DORIAN PALACEK</text>
      <text class="holder-title" x="460" y="140">PRESIDENT</text>
    </g>

    <g class="contacts">
      <g transform="translate(469 172)">
        <circle r="8" fill="none" stroke="var(--navy)" stroke-width="1.5"/>
        <path d="M-3.5 -3.5 q-1 3 2 6 q3 3 6 2 l-0.5 -2 -2 -0.5 -1 1 q-2 -1 -3 -3 l1 -1 -0.5 -2 z" fill="var(--navy)"/>
      </g>
      <text class="contact-line" x="486" y="178">012-555-0147</text>

      <g transform="translate(469 198)">
        <circle r="8" fill="none" stroke="var(--navy)" stroke-width="1.5"/>
        <rect x="-2.8" y="-4.5" width="5.6" height="9" rx="1" fill="none" stroke="var(--navy)" stroke-width="1.3"/>
      </g>
      <text class="contact-line" x="486" y="204">012-555-0147</text>

      <g transform="translate(469 225)">
        <circle r="8" fill="none" stroke="var(--navy)" stroke-width="1.5"/>
        <rect x="-4.5" y="-3" width="9" height="6.5" fill="var(--navy)"/>
        <path d="M-4.5 -3 L0 1 L4.5 -3" fill="none" stroke="var(--white)" stroke-width="1"/>
      </g>
      <text class="contact-line" x="486" y="231">info@skyvornq.com</text>

      <g transform="translate(469 252)" fill="none" stroke="var(--navy)" stroke-width="1.2">
        <circle r="8"/>
        <ellipse rx="3.5" ry="8"/>
        <line x1="-8" y1="0" x2="8" y2="0"/>
        <line x1="-7" y1="-4" x2="7" y2="-4"/>
        <line x1="-7" y1="4" x2="7" y2="4"/>
      </g>
      <text class="contact-line" x="486" y="258">www.skyvornq.com</text>
    </g>

    <path class="swoosh" d="M0 281 C 180 340, 380 378, 632 373 C 420 379, 200 343, 0 300 Z" fill="url(#swoosh-gradient)"/>
    <path class="footer-band" d="M0 311 C 150 360, 330 390, 507 383 C 620 378, 700 370, 762 359 L762 435 L0 435 Z" fill="var(--navy-deep)"/>

    <g class="address">
      <g transform="translate(216 416)" fill="none" stroke="var(--white)" stroke-width="1.5">
        <path d="M0 7 C -4 2, -6 -1, -6 -3 A6 6 0 0 1 6 -3 C 6 -1, 4 2, 0 7 Z"/>
        <circle cx="0" cy="-3" r="2"/>
      </g>
      <text class="address-line" x="232" y="422">4827 Trellis Hollow Road, Fort Pierce, Florida, 34951</text>
    </g>
  </svg>
</div>

<div class="card card-back">
  <svg viewBox="0 0 762 435" xmlns="http://www.w3.org/2000/svg">
    <g class="brand-block">
      <circle cx="381" cy="185" r="66" fill="none" stroke="var(--white)" stroke-width="7"/>
      <text class="brand-name" x="381" y="320" text-anchor="middle" font-size="50" fill="var(--white)" letter-spacing="7">SkyvornQ</text>
    </g>
    <text class="back-url" x="381" y="387" text-anchor="middle">www.skyvornq.com</text>
  </svg>
</div>

</body>
</html>
```